Tidewell Homecare

I am looking to have a website designed for a housekeeping company that looks similar to this one. https://marloweshomecare.example/

I need 5 websites designed but will start with this one to see how I like it.

Industry/Entity Type

House Cleaning

Coding

Coded - Design and coding required

Number of Pages Required

5+ page

Font styles to use
Serif
Script

Colors
ffffff
fdf9cf
fbf289
fbee3f
d6edf3
86cae7
33a6d7
edf1f8
cedeed

```html
<!DOCTYPE html>
<html lang="en">
<head>
<meta charset="utf-8">
<title>Tidewell Homecare</title>
<link href="https://fonts.googleapis.com/css2?family=Lato:wght@400;700;900&family=Open+Sans:wght@400;700;800&family=Oswald:wght@500&display=swap" rel="stylesheet">
<style>
:root{
  --blue:#2d9ad6;
  --sky:#6dbde6;
  --mist:#edf1f8;
  --yellow:#fbee3f;
  --ink:#2b2b2b;
  --text:#555;
  --panel:#2d2d2d;
  --grey-band:#f1f1f1;
  --white:#fff;
}
*{box-sizing:border-box;margin:0;padding:0}
html,body{width:1200px;height:4004px;overflow:hidden}
body{position:relative;font-family:"Lato",sans-serif;color:var(--text);background:var(--white)}
.abs{position:absolute}
.center{left:0;width:1200px;text-align:center}

.topbar{top:0;left:0;width:1200px;height:61px;background:var(--mist)}
.topbar-accent{top:0;left:0;width:362px;height:61px;background:var(--sky);clip-path:polygon(0 0,100% 0,88% 100%,0 100%)}
.social-dot{width:16px;height:16px;border-radius:50%;background:var(--white);top:22px}
.topbar-call{top:17px;left:588px;font-size:16px;color:var(--ink);font-weight:700}
.topbar-call b{font-size:22px;font-weight:700;vertical-align:-2px}
.topbar-mail{top:19px;left:908px;font-size:15px;color:var(--ink)}

.logo{font-family:"Oswald",sans-serif;font-weight:500;color:var(--blue);letter-spacing:.5px}
.header-logo{top:100px;left:75px;font-size:35px;line-height:1}
.nav{top:113px;left:564px}
.nav a{font-size:17px;color:#333;text-decoration:none;position:absolute;white-space:nowrap}
.nav a.active{color:var(--blue)}
.nav a.active::after{content:"";position:absolute;left:0;right:0;top:31px;height:2px;background:var(--blue)}

.hero{top:184px;left:0;width:1200px;height:702px;
  background:
    radial-gradient(ellipse 260px 340px at 370px 420px,#3a6fb0 0%,rgba(58,111,176,0) 70%),
    radial-gradient(ellipse 180px 300px at 1030px 420px,#2f5f9c 0%,rgba(47,95,156,0) 70%),
    radial-gradient(ellipse 300px 200px at 300px 650px,#f3f4f2 0%,rgba(243,244,242,0) 70%),
    linear-gradient(90deg,#6f7a82 0%,#c9cccb 35%,#bdb6ae 65%,#8a8683 100%)}
.hero-shade{top:184px;left:0;width:1200px;height:702px;background:rgba(0,0,0,.22)}
.hero-title{top:360px;font-family:"Open Sans",sans-serif;font-weight:800;font-size:74px;line-height:72px;color:var(--white);text-shadow:0 2px 6px rgba(0,0,0,.3)}
.hero-sub{top:536px;font-size:21px;line-height:33px;color:var(--white);font-weight:700;text-shadow:0 1px 4px rgba(0,0,0,.4)}
.btn{position:absolute;border-radius:30px;font-weight:700;font-size:17px;color:var(--ink);background:var(--yellow);display:flex;align-items:center;justify-content:center;gap:6px}
.btn .dot{width:13px;height:13px;border-radius:50%;background:var(--ink);position:relative}
.btn .dot::after{content:"";position:absolute;left:4px;top:3px;border-left:6px solid var(--yellow);border-top:3.5px solid transparent;border-bottom:3.5px solid transparent}
.hero-dot{top:832px;width:11px;height:11px;border-radius:50%;background:var(--white)}

.section-title{font-weight:900;font-size:33px;color:var(--ink);letter-spacing:.3px}

.about-photo{top:1012px;left:75px;width:1050px;height:356px;
  background:
    radial-gradient(ellipse 130px 110px at 150px 110px,#3b8be6 0%,rgba(59,139,230,0) 75%),
    radial-gradient(ellipse 120px 170px at 420px 150px,#2a6fd0 0%,rgba(42,111,208,0) 75%),
    radial-gradient(ellipse 90px 150px at 690px 160px,#e9eef2 0%,rgba(233,238,242,0) 75%),
    radial-gradient(ellipse 120px 120px at 950px 150px,#f4f6f8 0%,rgba(244,246,248,0) 75%),
    linear-gradient(90deg,#3b2a1e,#5a3e2a 50%,#3a281c)}
.about-card{top:1293px;left:92px;width:1018px;height:175px;background:var(--white)}
.about-text{top:1319px;left:92px;width:1018px;font-size:15.5px;line-height:30.5px;text-align:center;color:#444}

.svc{top:1633px;height:533px;width:600px}
.svc-res{left:0;background:radial-gradient(ellipse 220px 300px at 260px 170px,#4a4a4a 0%,rgba(74,74,74,0) 75%),linear-gradient(90deg,#262626,#363636)}
.svc-com{left:600px;background:radial-gradient(ellipse 240px 300px at 380px 200px,#4aa8e0 0%,rgba(74,168,224,0) 75%),linear-gradient(90deg,#2a8ccd,#3597d6)}
.svc-icon{top:1712px}
.svc-title{font-size:34px;font-weight:900;color:var(--white);top:1793px}
.svc-text{top:1850px;font-size:15.5px;line-height:28.7px;color:#eaeaea;width:500px}
.btn-outline{position:absolute;top:2035px;height:60px;width:178px;border:2px solid var(--yellow);border-radius:30px;color:var(--yellow);font-weight:700;font-size:17px;display:flex;align-items:center;justify-content:center;gap:6px}
.btn-outline .dot{width:13px;height:13px;border-radius:50%;background:var(--yellow);position:relative}
.btn-outline .dot::after{content:"";position:absolute;left:4px;top:3px;border-left:6px solid #333;border-top:3.5px solid transparent;border-bottom:3.5px solid transparent}

.testi-text{top:2332px;font-size:20.5px;line-height:37px;color:#444}
.testi-name{top:2464px;font-size:18px;color:var(--blue);letter-spacing:.5px}

.blog-band{top:2569px;left:0;width:1200px;height:710px;background:var(--grey-band)}
.blog-img{top:2715px;width:512px;height:275px}
.blog-title{top:3017px;font-size:22px;font-weight:700;color:#222;letter-spacing:.2px}
.blog-meta{top:3057px;font-size:13.5px;color:var(--blue);font-weight:700}
.blog-text{top:3081px;font-size:14px;line-height:27.5px;color:#555;width:530px}
.blog-more{top:3173px;font-size:15px;font-weight:700;color:var(--blue)}

.est-photo{top:3279px;left:0;width:587px;height:451px;
  background:
    radial-gradient(ellipse 260px 170px at 290px 290px,#3f86cc 0%,rgba(63,134,204,0) 75%),
    radial-gradient(ellipse 280px 90px at 290px 150px,#e7d3c3 0%,rgba(231,211,195,0) 75%),
    linear-gradient(180deg,#f6f7f8,#eceff2)}
.est-panel{top:3279px;left:587px;width:613px;height:451px;background:var(--panel)}
.est-title{top:3338px;left:614px;font-size:34px;font-weight:900;color:var(--white)}
.field{position:absolute;background:var(--white);border-radius:4px;font-size:11px;color:#444;padding:14px 15px;text-transform:uppercase}

.foot-logo{top:3812px;left:75px;font-size:27px}
.foot-small{font-size:12.5px;color:#444;line-height:22px}
.foot-head{top:3793px;font-size:14.5px;font-weight:700;color:#111}
.foot-list{top:3816px;font-size:13.5px;line-height:27.8px;color:#333}
.foot-social{top:3943px;width:18px;height:18px;border-radius:50%;background:#333}
</style>
</head>
<body>

<div class="abs topbar"></div>
<div class="abs topbar-accent"></div>
<div class="abs social-dot" style="left:74px"></div>
<div class="abs social-dot" style="left:110px"></div>
<div class="abs social-dot" style="left:150px"></div>
<div class="abs social-dot" style="left:190px"></div>
<div class="abs social-dot" style="left:230px"></div>
<div class="abs topbar-call">
  <svg width="16" height="16" viewBox="0 0 24 24" style="vertical-align:-2px;margin-right:6px"><path d="M6.6 10.8a15 15 0 0 0 6.6 6.6l2.2-2.2a1 1 0 0 1 1-.25 11.4 11.4 0 0 0 3.6.57 1 1 0 0 1 1 1V20a1 1 0 0 1-1 1A17 17 0 0 1 3 4a1 1 0 0 1 1-1h3.5a1 1 0 0 1 1 1c0 1.25.2 2.45.57 3.57a1 1 0 0 1-.25 1z" fill="none" stroke="#333" stroke-width="1.8"/></svg>CALL NOW : <b>1-800-555-0142</b>
</div>
<div class="abs topbar-mail">
  <svg width="16" height="12" viewBox="0 0 16 12" style="vertical-align:-1px;margin-right:8px"><rect x="1" y="1" width="14" height="10" fill="none" stroke="#333" stroke-width="1.4"/><path d="M1 1l7 6 7-6" fill="none" stroke="#333" stroke-width="1.4"/></svg>hello@tidewellhomecare.example
</div>

<div class="abs logo header-logo">TIDEWELL HOMECARE</div>
<nav class="abs nav">
  <a class="active" style="left:0">HOME</a>
  <a style="left:101px">SERVICES</a>
  <a style="left:227px">GIFT CARDS</a>
  <a style="left:374px">ABOUT</a>
  <a style="left:481px">CONTACT</a>
</nav>

<div class="abs hero" role="img" aria-label="Photo of smiling cleaning staff in blue uniforms tidying a bright office"></div>
<div class="abs hero-shade"></div>
<h1 class="abs center hero-title">Welcome to<br>Tidewell Homecare</h1>
<p class="abs center hero-sub">Orci varius natoque penatibus et magnis dis parturient montes, nascetur<br>ridiculus mus nec molestie dolor.</p>
<div class="btn" style="top:634px;left:513px;width:177px;height:59px">READ MORE <span class="dot"></span></div>
<div class="abs hero-dot" style="left:556px;background:var(--blue)"></div>
<div class="abs hero-dot" style="left:582px"></div>
<div class="abs hero-dot" style="left:608px"></div>
<div class="abs hero-dot" style="left:633px"></div>

<h2 class="abs center section-title" style="top:943px">ABOUT TIDEWELL HOMECARE</h2>
<div class="abs about-photo" role="img" aria-label="Cleaning supplies: sponge, rubber gloves, spray bottle and duster on a wooden surface"></div>
<div class="abs about-card"></div>
<p class="abs about-text">Lorem ipsum dolor sit amet, consectetur adipiscing elit. Sed nunc nibh, facilisis lacinia convallis pharetra, interdum vitae nisi.<br>Ut maximus vel leo eu venenatis. Vivamus eu ipsum purus. Donec pulvinar ornare dui sed rhoncus. Etiam id sapien quis elit fringilla<br>pellentesque id at lectus. Ut eu cursus mauris. Orci varius natoque penatibus et magnis dis parturient montes,<br>nascetur ridiculus mus ed nec molestie dolor, non pulvinar metus.</p>
<div class="btn" style="top:1491px;left:514px;width:174px;height:58px">READ MORE <span class="dot"></span></div>

<div class="abs svc svc-res" role="img" aria-label="Dim photo of a cleaner at work in a home"></div>
<div class="abs svc svc-com" role="img" aria-label="Blue-tinted photo of cleaners working in an office"></div>
<svg class="abs svc-icon" style="left:75px" width="68" height="66" viewBox="0 0 68 66" fill="none" stroke="#fff" stroke-width="2.5" stroke-linejoin="round" stroke-linecap="round" aria-label="Home cleaning icon">
  <path d="M12 30 L32 12 L52 30"/><path d="M17 26 V44 H47 V26"/><rect x="27" y="32" width="10" height="12"/>
  <path d="M2 52 H20 L30 58 H48 L62 48"/><path d="M2 62 H22 L34 66"/>
  <path d="M56 6 v8 M52 10 h8"/><path d="M8 10 v6 M5 13 h6"/><path d="M60 22 v5 M57.5 24.5 h5"/>
</svg>
<svg class="abs svc-icon" style="left:651px" width="86" height="66" viewBox="0 0 86 66" fill="none" stroke="#fff" stroke-width="2.5" stroke-linejoin="round" stroke-linecap="round" aria-label="Office cleaning icon">
  <rect x="40" y="4" width="38" height="26"/><path d="M59 30 v8 M50 38 h18"/>
  <path d="M2 44 H84"/><path d="M10 44 V64 M76 44 V64"/>
  <rect x="18" y="20" width="14" height="16"/><path d="M14 38 H36 M25 38 V62 M17 62 H33"/>
  <path d="M8 6 v8 M4 10 h8"/><path d="M50 52 v8 M46 56 h8"/>
</svg>
<h3 class="abs svc-title" style="left:77px">RESIDENTIAL CLEANING</h3>
<h3 class="abs svc-title" style="left:650px">COMMERCIAL CLEANING</h3>
<p class="abs svc-text" style="left:79px">Lorem ipsum dolor sit amet, consectetur adipiscing elit.<br>Sed nunc nibh, facilisis lacinia convallis pharetra, interdum vitae<br>nisi. Ut maximus vel leo eu venenatis. Vivamus eu ipsum purus.<br>Donec pulvinar ornare dui sed rhoncus. Etiam id sapien<br>quis elit fringilla pellentesque id at lectus.</p>
<p class="abs svc-text" style="left:651px">Lorem ipsum dolor sit amet, consectetur adipiscing elit.<br>Sed nunc nibh, facilisis lacinia convallis pharetra, interdum vitae<br>nisi. Ut maximus vel leo eu venenatis. Vivamus eu ipsum purus.<br>Donec pulvinar ornare dui sed rhoncus. Etiam id sapien<br>quis elit fringilla pellentesque id at lectus.</p>
<div class="btn-outline" style="left:78px">READ MORE <span class="dot"></span></div>
<div class="btn-outline" style="left:651px">READ MORE <span class="dot"></span></div>

<h2 class="abs center section-title" style="top:2235px">TESTIMONIALS</h2>
<svg class="abs" style="top:2290px;left:88px" width="82" height="52" viewBox="0 0 82 52" fill="#d2d2d2" aria-hidden="true">
  <circle cx="17" cy="36" r="15"/><path d="M2 36 C2 16 14 4 32 0 L33 6 C22 10 16 18 16 30 Z"/>
  <circle cx="61" cy="36" r="15"/><path d="M46 36 C46 16 58 4 76 0 L77 6 C66 10 60 18 60 30 Z"/>
</svg>
<svg class="abs" style="top:2400px;left:1032px" width="82" height="52" viewBox="0 0 82 52" fill="#d2d2d2" aria-hidden="true">
  <circle cx="21" cy="16" r="15"/><path d="M36 16 C36 36 24 48 6 52 L5 46 C16 42 22 34 22 22 Z"/>
  <circle cx="65" cy="16" r="15"/><path d="M80 16 C80 36 68 48 50 52 L49 46 C60 42 66 34 66 22 Z"/>
</svg>
<svg class="abs" style="top:2354px;left:58px" width="16" height="24" viewBox="0 0 16 24"><path d="M13 2L3 12l10 10" fill="none" stroke="#555" stroke-width="3"/></svg>
<svg class="abs" style="top:2354px;left:1124px" width="16" height="24" viewBox="0 0 16 24"><path d="M3 2l10 10-10 10" fill="none" stroke="#555" stroke-width="3"/></svg>
<p class="abs center testi-text">Orci varius natoque penatibus et magnis dis parturient montes, nascetur ridiculus mus.<br>Sed nec molestie dolor, non pulvinar metus. Praesent vehicula felis quis dolor<br>posuere, non rutrum diam consequat.</p>
<div class="abs center testi-name">DARA M</div>

<div class="abs blog-band"></div>
<h2 class="abs center section-title" style="top:2634px">LATEST BLOG</h2>
<svg class="abs" style="top:2980px;left:47px" width="14" height="22" viewBox="0 0 14 22"><path d="M11 2L3 11l8 9" fill="none" stroke="#555" stroke-width="3"/></svg>
<svg class="abs" style="top:2980px;left:1139px" width="14" height="22" viewBox="0 0 14 22"><path d="M3 2l8 9-8 9" fill="none" stroke="#555" stroke-width="3"/></svg>
<div class="abs blog-img" style="left:75px;background:radial-gradient(ellipse 110px 100px at 330px 170px,#7ccc34 0%,rgba(124,204,52,0) 80%),radial-gradient(ellipse 140px 70px at 320px 60px,#f0b84a 0%,rgba(240,184,74,0) 80%),linear-gradient(180deg,#e9ecef,#d8dde2)" role="img" aria-label="Bucket of colourful cleaning products and brushes"></div>
<div class="abs blog-img" style="left:614px;background:radial-gradient(ellipse 110px 140px at 170px 150px,#2f6cc0 0%,rgba(47,108,192,0) 80%),linear-gradient(160deg,#dcdcd8 0%,#b8beb9 45%,#4a4b42 75%,#2e2f29 100%)" role="img" aria-label="Worker on a ladder cleaning house gutters"></div>

<h3 class="abs blog-title" style="left:74px">CURABITUR RHONCUS MATTIS IPSUM</h3>
<h3 class="abs blog-title" style="left:614px">CURABITUR RHONCUS MATTIS IPSUM</h3>
<div class="abs blog-meta" style="left:74px"><span style="display:inline-block;width:12px;height:12px;border:2px solid var(--blue);margin-right:14px;vertical-align:-1px"></span>APRIL 15, 2020 &nbsp;&nbsp; <span style="display:inline-block;width:11px;height:11px;border-radius:50%;background:var(--blue);margin-right:6px;vertical-align:-1px"></span>BY ADMIN</div>
<div class="abs blog-meta" style="left:614px"><span style="display:inline-block;width:12px;height:12px;border:2px solid var(--blue);margin-right:14px;vertical-align:-1px"></span>APRIL 15, 2020 &nbsp;&nbsp; <span style="display:inline-block;width:11px;height:11px;border-radius:50%;background:var(--blue);margin-right:6px;vertical-align:-1px"></span>BY ADMIN</div>
<p class="abs blog-text" style="left:74px">Nemo enim ipsam voluptatem quia voluptas sit aspernatur aut odit aut<br>fugit, sed quia consequuntur magni dolores eos qui ratione Lorem Ipsum is<br>simply dummy text of the printing and typesetting industry.</p>
<p class="abs blog-text" style="left:614px">Nemo enim ipsam voluptatem quia voluptas sit aspernatur aut odit aut<br>fugit, sed quia consequuntur magni dolores eos qui ratione Lorem Ipsum is<br>simply dummy text of the printing and typesetting industry.</p>
<div class="abs blog-more" style="left:74px">READ MORE &rsaquo;&rsaquo;</div>
<div class="abs blog-more" style="left:614px">READ MORE &rsaquo;&rsaquo;</div>

<div class="abs est-photo" role="img" aria-label="Team of cleaners in blue aprons with mops, buckets and a vacuum"></div>
<div class="abs est-panel"></div>
<h2 class="abs est-title">GET FREE ESTIMATE</h2>
<div class="field" style="top:3402px;left:614px;width:249px;height:48px">Enter Full Name</div>
<div class="field" style="top:3402px;left:878px;width:249px;height:48px">Phone No</div>
<div class="field" style="top:3461px;left:614px;width:513px;height:47px">Enter Email Address</div>
<div class="field" style="top:3518px;left:614px;width:513px;height:83px;padding-top:12px">Message</div>
<div class="btn" style="top:3616px;left:614px;width:180px;height:51px">SUBMIT</div>

<div class="abs logo foot-logo">TIDEWELL HOMECARE</div>
<p class="abs foot-small" style="top:3856px;left:75px">Copyright © 2020. Tidewell Homecare.<br>All Right Reserved</p>

<div class="abs foot-head" style="left:334px">SITE MAP</div>
<div class="abs foot-list" style="left:334px">Home<br>Services<br>Gift Cards<br>About<br>Contact</div>

<div class="abs foot-head" style="left:476px">SERVICES</div>
<div class="abs foot-list" style="left:476px">Orci varius<br>Natoque penatibus<br>Magnis dis<br>Parturient montes</div>

<div class="abs foot-head" style="left:650px">CONTACT INFO</div>
<svg class="abs" style="top:3822px;left:650px" width="10" height="14" viewBox="0 0 10 14"><path d="M5 0a5 5 0 0 1 5 5c0 4-5 9-5 9S0 9 0 5a5 5 0 0 1 5-5z" fill="#333"/><circle cx="5" cy="5" r="1.8" fill="#fff"/></svg>
<div class="abs foot-small" style="top:3819px;left:684px;font-size:13.5px">42 Harbour Lane,<br>Saltmere,<br>SM4 7QT</div>
<svg class="abs" style="top:3897px;left:650px" width="12" height="12" viewBox="0 0 24 24"><path d="M6.6 10.8a15 15 0 0 0 6.6 6.6l2.2-2.2a1 1 0 0 1 1-.25 11.4 11.4 0 0 0 3.6.57 1 1 0 0 1 1 1V20a1 1 0 0 1-1 1A17 17 0 0 1 3 4a1 1 0 0 1 1-1h3.5a1 1 0 0 1 1 1c0 1.25.2 2.45.57 3.57a1 1 0 0 1-.25 1z" fill="#333"/></svg>
<div class="abs foot-small" style="top:3892px;left:684px;font-size:13.5px">1-800-555-0142</div>
<svg class="abs" style="top:3929px;left:650px" width="13" height="10" viewBox="0 0 16 12"><rect x="0" y="0" width="16" height="12" fill="#333"/><path d="M0 0l8 6 8-6" fill="none" stroke="#fff" stroke-width="1.4"/></svg>
<div class="abs foot-small" style="top:3922px;left:684px;font-size:12.5px">hello@tidewellhomecare.example</div>

<div class="abs foot-head" style="left:884px">EMAIL SIGN UP</div>
<div class="field" style="top:3829px;left:884px;width:243px;height:37px;border:1px solid #bbb;padding:11px 18px;text-transform:none;font-size:11.5px">Enter Email Address</div>
<div class="abs" style="top:3876px;left:1029px;width:96px;height:39px;border-radius:20px;background:var(--blue);color:#fff;font-size:12.5px;font-weight:700;display:flex;align-items:center;justify-content:center">SIGN UP</div>
<div class="abs foot-social" style="left:882px"></div>
<div class="abs foot-social" style="left:917px"></div>
<div class="abs foot-social" style="left:957px"></div>
<div class="abs foot-social" style="left:997px"></div>
<div class="abs foot-social" style="left:1037px"></div>

</body>
</html>
```